Flyer to advertise gutter cleaning throughout the Autumn and winter monthss

I need a new flyer to advertise gutter and driveway cleaning, roof and gutter repairs.

I am an experienced licensed Plumber and Gasfitter looking to broaden my scope of work to gutter cleaning. I am experienced in cleaning gutter and live in a area with large gum trees. I wont something that's clear, eye catching but not too busy.

Flyer requirements: Free roof inspection - no obligation. Gutter Cleaning from $199. Pictures of men using blower or hands to clean roof gutters (no obvious faces) to be included. Australian looking houses.

A mention that 'All general plumbing maintenance' is offered as other services but not too much wording about this as the target is for gutter cleaning.

Phone number: 0427 385 912 (in this format)
Business Name: Larkvale Plumbing & Gasfitting
License: 3175420
ABN: 71364058227
Web: http://larkvaleplumbing.example.site/

Target Market(s)

Elderly - busy working class

Industry/Entity Type

Plumber

Font styles to use
Sans Serif

Colors
0355a3
fbed22
ec1f27
f78f20

Requirements
Must have
• Roof Gutter Cleaning pictures
• Men in protective clothing if possible
Nice to have
• More information:
• Prevent against flooding, mold, rust, rotting and corrosion now!
• Gutter Cleaning Services
• • Remove leaves, sticks, and other debris
• • Clear away clogs
• • Test your downpipes
• • Pinpoint any gutter issues
• • Repair gutter
• With regular service, you can count on your property to be well-protected no matter what the forecast!
Should not have
• Houses that don't look Australian

```html
<!DOCTYPE html>
<html lang="en">
<head>
<meta charset="utf-8">
<title>Larkvale Plumbing &amp; Gasfitting – Gutter and Driveway Cleaning Flyer</title>
<link rel="stylesheet" href="https://fonts.googleapis.com/css2?family=Open+Sans:ital,wght@0,400;0,600;0,700;0,800;1,400;1,600&family=Kaushan+Script&display=swap">
<style>
  :root {
    --navy: #27236a;
    --red: #e8194a;
    --yellow: #f1e933;
    --teal: #127470;
    --paper: #ebebeb;
    --backdrop: #e4e4e4;
    --ink: #1d1b3f;
    --strip: #3a3a3a;
    --white: #ffffff;
  }
  * { box-sizing: border-box; margin: 0; padding: 0; }
  html, body { width: 1200px; height: 1000px; overflow: hidden; }
  body { background: var(--backdrop); font-family: "Open Sans", sans-serif; position: relative; }

  .flyer {
    position: absolute; left: 280px; top: 47px;
    width: 640px; height: 905px;
    background: var(--paper);
    overflow: hidden;
    box-shadow: 0 4px 18px rgba(0,0,0,0.18);
  }

  .header-panel {
    position: absolute; left: 0; top: 0; width: 370px; height: 392px;
    background: var(--navy);
  }
  .brand { position: absolute; left: 34px; top: 52px; display: flex; align-items: center; gap: 10px; }
  .brand-dot { width: 30px; height: 30px; border-radius: 50%; background: var(--red); }
  .brand-name { color: var(--white); font-weight: 600; font-size: 11px; letter-spacing: 0.3px; line-height: 1.2; text-transform: uppercase; }
  .brand-rule { position: absolute; left: 34px; top: 112px; width: 100px; height: 5px; background: var(--red); }

  .headline {
    position: absolute; left: 32px; top: 128px;
    color: var(--white); font-weight: 800; font-size: 47px; line-height: 1.0;
    letter-spacing: 0.5px; text-transform: uppercase;
  }
  .price { position: absolute; left: 36px; top: 290px; display: flex; align-items: baseline; gap: 10px; }
  .price-from { font-family: "Kaushan Script", cursive; color: var(--white); font-size: 44px; }
  .price-amount { color: var(--yellow); font-weight: 800; font-size: 62px; letter-spacing: -1px; }

  .other-services {
    position: absolute; left: 0; top: 392px; width: 370px; height: 132px;
    background: var(--red);
    padding: 22px 0 0 38px;
    color: var(--white); font-style: italic; font-size: 11.5px; line-height: 1.35;
    list-style: none;
  }

  .services { position: absolute; left: 55px; top: 540px; }
  .services-title { color: var(--ink); font-weight: 700; font-size: 26px; letter-spacing: 0.3px; margin-bottom: 6px; }
  .services-list { list-style: none; }
  .services-list li { display: flex; align-items: center; gap: 8px; color: var(--ink); font-size: 17px; line-height: 29px; }
  .services-list svg { width: 11px; height: 11px; }

  .contact { position: absolute; left: 20px; width: 320px; top: 748px; text-align: center; }
  .contact-cta { color: var(--navy); font-weight: 800; font-size: 20px; line-height: 1.15; text-transform: uppercase; }
  .contact-phone { color: var(--red); font-weight: 800; font-size: 37px; line-height: 1.2; margin-top: 6px; }
  .contact-web { color: var(--navy); font-weight: 700; font-size: 12px; }

  .photo { position: absolute; }
  .photo-roof {
    left: 370px; top: 0; width: 270px; height: 582px;
    background: linear-gradient(170deg, #6c7d95 0%, #55657e 35%, #4a5670 55%, #8a6a45 75%, #e0842c 85%, #d9c85a 93%, #e8e8e8 100%);
  }
  .photo-hands {
    left: 368px; top: 592px; width: 268px; height: 112px;
    background: linear-gradient(100deg, #a9683f 0%, #b89a78 30%, #8b5e38 55%, #7d7a76 80%, #9a9793 100%);
  }
  .photo-driveway {
    left: 368px; top: 712px; width: 268px; height: 126px;
    background: linear-gradient(180deg, #4d6a33 0%, #5d7c3c 22%, #9e6a58 45%, #b07664 75%, #8f5d4e 100%);
  }
  .license-strip {
    position: absolute; left: 390px; top: 850px; width: 250px; height: 36px;
    background: var(--strip);
    color: var(--white); font-size: 10.5px;
    display: flex; align-items: center; justify-content: flex-end; padding-right: 12px;
  }

  .guarantee-badge { position: absolute; left: 282px; top: 342px; width: 190px; height: 190px; }
  .badge-text { font-family: "Open Sans", sans-serif; font-weight: 800; fill: var(--white); }
</style>
</head>
<body>
  <article class="flyer">
    <section class="header-panel">
      <div class="brand">
        <span class="brand-dot"></span>
        <span class="brand-name">Larkvale Plumbing<br>&amp; Gasfitting</span>
      </div>
      <div class="brand-rule"></div>
      <h1 class="headline">Gutter and<br>Driveway<br>Cleaning</h1>
      <div class="price">
        <span class="price-from">From</span>
        <span class="price-amount">$199</span>
      </div>
    </section>

    <ul class="other-services">
      <li>Plumbing Maintenance, Sewer &amp; Stormwater</li>
      <li>High Pressure Cleaning, Hot Water Systems</li>
      <li>Renovations, Blocked Drains - Jet Rodding</li>
      <li>TMV Testing, Backflow Testing &amp; Prevention</li>
      <li>Gasfitting and Appliance Installation</li>
    </ul>

    <section class="services">
      <h2 class="services-title">OUR SERVICES</h2>
      <ul class="services-list">
        <li><svg viewBox="0 0 12 12"><path d="M1 6 L4.5 10 L11 1.5" fill="none" stroke="#e8194a" stroke-width="2"/></svg>Gutter cleaning</li>
        <li><svg viewBox="0 0 12 12"><path d="M1 6 L4.5 10 L11 1.5" fill="none" stroke="#e8194a" stroke-width="2"/></svg>Driveway cleaning</li>
        <li><svg viewBox="0 0 12 12"><path d="M1 6 L4.5 10 L11 1.5" fill="none" stroke="#e8194a" stroke-width="2"/></svg>Roof repairs</li>
        <li><svg viewBox="0 0 12 12"><path d="M1 6 L4.5 10 L11 1.5" fill="none" stroke="#e8194a" stroke-width="2"/></svg>Gutter repairs</li>
      </ul>
    </section>

    <section class="contact">
      <p class="contact-cta">Call for free<br>roof inspection</p>
      <p class="contact-phone">0427 385 912</p>
      <p class="contact-web">www.larkvaleplumbing.example.site</p>
    </section>

    <div class="photo photo-roof" role="img" aria-label="Close-up of grey roof shingles with autumn leaves in a gutter"></div>
    <div class="photo photo-hands" role="img" aria-label="Gloved hand removing leaves from a roof gutter"></div>
    <div class="photo photo-driveway" role="img" aria-label="Worker pressure-washing a paved driveway beside a hedge"></div>
    <div class="license-strip">License: 3175420 | ABN: 71364058227</div>

    <svg class="guarantee-badge" viewBox="0 0 190 190" aria-label="All work guaranteed">
      <defs>
        <path id="badge-arc-top" d="M27 95 A68 68 0 0 1 163 95"/>
        <path id="badge-arc-bottom" d="M13 95 A82 82 0 0 0 177 95"/>
      </defs>
      <circle cx="95" cy="95" r="92" fill="var(--teal)"/>
      <circle cx="95" cy="95" r="88" fill="none" stroke="#ffffff" stroke-width="2"/>
      <circle cx="95" cy="95" r="48" fill="#ffffff"/>
      <text class="badge-text" font-size="24" letter-spacing="2" text-anchor="middle">
        <textPath href="#badge-arc-top" startOffset="50%">ALL WORK</textPath>
      </text>
      <text class="badge-text" font-size="20" letter-spacing="2" text-anchor="middle">
        <textPath href="#badge-arc-bottom" startOffset="50%">GUARANTEED</textPath>
      </text>
      <path d="M68 96 L87 116 L126 62" fill="none" stroke="var(--yellow)" stroke-width="13" stroke-linecap="round" stroke-linejoin="round"/>
    </svg>
  </article>
</body>
</html>
```